Boutique custom software development company needs new business card

Our nearly 20 year old custom software development company would like to better include the fact that we are now providing Bitcoin services. These new services are B2B include education (how to acquire and securely hold Bitcoin) and integrating Bitcoin payments into existing ecommerce sites or other existing systems. Please keep the card clean and simple. Attached is our current design and some other files. vextorial.com

Target Market(s)

businesses owners interested in long term relationship

Industry/Entity Type

Custom software development and Bitcoin

Contact Information for Business Card

Dale Parker, dale@vextorial.com, vextorial.com, (888) 555-VXTRL

Font styles to use
Other font styles liked:
• monospace

Requirements
Must have
• double-sided
Nice to have
• clean and simple
Should not have
• physical address

```html
<!DOCTYPE html>
<html lang="en">
<head>
<meta charset="utf-8">
<title>Vextorial Business Card</title>
<link rel="stylesheet" href="https://fonts.googleapis.com/css2?family=Montserrat:wght@400;500;700;800&display=swap">
<style>
  :root {
    --stage: #3b3b3b;
    --card: #121212;
    --card-edge: #3d6fc4;
    --blue: #3f78cc;
    --orange: #f07a1e;
    --white: #e8e8e8;
    --mark-shade: #2a2a2a;
  }
  * { margin: 0; padding: 0; box-sizing: border-box; }
  html, body {
    width: 1200px; height: 801px; overflow: hidden;
    background: var(--stage);
    font-family: "Montserrat", sans-serif;
  }
  .stage {
    width: 1200px; height: 801px;
    display: flex; align-items: center; justify-content: center; gap: 50px;
  }
  .card {
    position: relative;
    width: 540px; height: 309px;
    background: var(--card);
    border-bottom: 3px solid var(--card-edge);
    box-shadow: 0 18px 30px rgba(0,0,0,0.45);
    overflow: hidden;
  }
  .brand {
    position: absolute; right: 52px; top: 40px;
    text-align: right;
  }
  .brand-name {
    color: var(--blue);
    font-weight: 800; font-size: 38px; letter-spacing: -1px; line-height: 1;
  }
  .brand-tagline {
    color: var(--blue);
    font-size: 12px; margin-top: 5px; line-height: 1.3;
  }
  .person-name {
    position: absolute; left: 52px; top: 204px;
    color: var(--blue); font-weight: 700; font-size: 19px; letter-spacing: 0.5px;
    text-transform: uppercase;
  }
  .divider {
    position: absolute; left: 52px; right: 70px; top: 232px;
    height: 1px; background: var(--blue);
  }
  .contacts {
    position: absolute; left: 52px; top: 244px;
    list-style: none; color: var(--white); font-size: 14px;
  }
  .contacts li { display: flex; align-items: center; gap: 8px; height: 22px; }
  .contacts svg { width: 12px; height: 12px; fill: var(--orange); flex: none; }
  .website {
    position: absolute; right: 30px; top: 258px;
    color: var(--white); font-size: 13px;
  }
  .website .accent { color: var(--orange); }
  .accent-bar {
    position: absolute; right: 0; bottom: 0;
    width: 160px; height: 12px; background: var(--orange);
  }
  .card-back { display: flex; align-items: center; justify-content: center; }
  .back-mark {
    color: var(--mark-shade);
    font-weight: 800; font-size: 52px; letter-spacing: -1px;
  }
</style>
</head>
<body>
<main class="stage">
  <section class="card card-front">
    <div class="brand">
      <div class="brand-name">VEXTORIAL</div>
      <div class="brand-tagline">custom applications &amp; bitcoin services</div>
    </div>
    <div class="person-name">Dale Parker</div>
    <div class="divider"></div>
    <ul class="contacts">
      <li>
        <svg viewBox="0 0 24 24" aria-hidden="true"><path d="M6.6 10.8a15 15 0 0 0 6.6 6.6l2.2-2.2c.3-.3.7-.4 1-.2 1.1.4 2.3.6 3.6.6.6 0 1 .4 1 1V20c0 .6-.4 1-1 1A17 17 0 0 1 3 4c0-.6.4-1 1-1h3.5c.6 0 1 .4 1 1 0 1.3.2 2.5.6 3.6.1.3 0 .7-.2 1z"/></svg>
        (888) 555-VXTRL
      </li>
      <li>
        <svg viewBox="0 0 24 24" aria-hidden="true"><path d="M2 5h20v14H2zm2 2v.5l8 5 8-5V7l-8 5z"/></svg>
        dale@vextorial.com
      </li>
    </ul>
    <div class="website">www.<span class="accent">vextorial</span>.com</div>
    <div class="accent-bar"></div>
  </section>

  <section class="card card-back">
    <div class="back-mark">VEXTORIAL</div>
  </section>
</main>
</body>
</html>
```